I need a flyer made , the flyer can be one page or two pages or three pages . I will be posting this on Instagram and social media platforms. I am a luxury home builder , I am looking to hire a construction project manager . Below are some examples and ideas what can be on the flyer

We’re looking for a construction project manager who’s passionate about building luxury homes at the highest standards
We’re hiring construction project manager
* Experience 5+ years in residential project management with a strong portfolio of completed homes.
* location : Bergen County NJ
* excellent leadership skills, leads teams with confidence and clarity
* communicates seamlessly with architects , engineers, designers and clients
*knows how to manage budgets and timelines without compromising quality
*solves problems with a positive solution first mindset
* pays attention to every detail because in luxury the small things are the big things

Apply now , link in bio or DM to connect.

My logo is attached, my web site www.velstridebuilders.com
My style is modern but still warm and inviting. I like a clean classy look .

Please don’t add any images of chairs or people to the flyer , I do not want people on my flyer. Do not add standard images of offices and houses , we are luxury builders , we build homes over 2 million dollars. Keep a classy , simple modern look . High end .

You can add a white hard hat with my logo on it for a image , this is a suggestion does not have to be on my flyer ,

```html
<!DOCTYPE html>
<html lang="en">
<head>
<meta charset="utf-8">
<title>Hiring – Construction Project Manager</title>
<link href="https://fonts.googleapis.com/css2?family=Montserrat:ital,wght@0,400;0,500;0,600;0,700;0,800;1,400;1,700&display=swap" rel="stylesheet">
<style>
  :root{
    --cream:#efe7da;
    --cream-light:#f4eee4;
    --bronze:#6b5a3c;
    --bronze-soft:#7a6a4b;
    --ink:#121110;
    --panel:#0b0a09;
    --white:#ffffff;
    --rule:#2a2622;
  }
  *{margin:0;padding:0;box-sizing:border-box}
  html,body{width:1200px;height:1200px;overflow:hidden;background:var(--cream)}
  body{font-family:'Montserrat',sans-serif;color:var(--ink)}
  .flyer{position:relative;width:1200px;height:1200px;overflow:hidden;
    background:linear-gradient(135deg,var(--cream-light) 0%,var(--cream) 55%,#e9e0d1 100%)}
  .abs{position:absolute;line-height:1;white-space:nowrap}

  .eyebrow{left:85px;top:58px;font-size:56px;font-weight:800;letter-spacing:.14em}
  .headline{left:78px;top:111px;font-size:206px;font-weight:700;color:var(--bronze);letter-spacing:-.01em}
  .role-kicker{left:81px;top:309px;font-size:37px;font-weight:500;letter-spacing:.13em}
  .role-title{left:81px;top:353px;font-size:66px;font-weight:700;letter-spacing:-.005em}

  .exp-number{left:81px;top:453px;font-size:78px;font-weight:800;letter-spacing:-.03em}
  .exp-years{left:179px;top:469px;font-size:36px;font-weight:700;letter-spacing:-.01em}
  .exp-label{left:184px;top:507px;font-size:21px;font-weight:600;color:var(--bronze)}
  .exp-field{left:327px;top:471px;font-size:28px;font-weight:600;line-height:27px}

  .portfolio-pill{position:absolute;left:83px;top:544px;width:560px;height:41px;border-radius:0 20px 20px 0;
    background:var(--bronze);color:var(--cream);font-size:23px;font-weight:500;letter-spacing:.02em;
    display:flex;align-items:center;padding-left:20px;white-space:nowrap}

  .requirements-panel{position:absolute;left:0;top:609px}
  .requirements{position:absolute;left:0;top:650px;list-style:none}
  .requirement{position:absolute;left:0;width:700px;height:74px}
  .requirement .tick{position:absolute;left:81px;top:9px;width:21px;height:21px}
  .requirement .title{position:absolute;left:122px;top:3px;font-size:23px;font-weight:800;color:var(--bronze-soft);line-height:1;white-space:nowrap}
  .requirement .detail{position:absolute;left:122px;top:29px;font-size:18.5px;font-weight:500;color:var(--white);line-height:1;white-space:nowrap}
  .requirement .divider{position:absolute;left:122px;top:62px;height:1px;background:var(--rule)}

  .tagline{left:85px;top:1067px;font-size:27px;font-style:italic;font-weight:400;letter-spacing:.07em}
  .tagline b{color:var(--bronze);font-weight:700}
  .website{left:84px;top:1107px;font-size:34px;font-weight:700}
  .website span{color:var(--bronze)}

  .brand{position:absolute;right:76px;top:70px;text-align:center;font-weight:500;color:var(--ink)}
  .brand .name{display:block;font-size:54px;letter-spacing:.04em;line-height:1}
  .brand .sub{display:block;font-size:17px;letter-spacing:.2em;margin-top:16px;line-height:1}

  .hero-photo{position:absolute;left:700px;top:196px;width:500px;height:652px;
    background:radial-gradient(ellipse at 55% 60%,#a9abad 0%,#c3c2bd 38%,rgba(223,214,198,.6) 70%,rgba(239,231,218,0) 100%)}

  .location-band{position:absolute;left:0;top:0}
  .location-label{right:76px;top:865px;font-size:26px;font-weight:500;letter-spacing:.14em;color:var(--cream)}
  .location-name{right:72px;top:897px;font-size:42px;font-weight:700;color:var(--white)}

  .cta{left:752px;top:971px;font-size:68px;font-weight:700;letter-spacing:-.01em}
  .cta-note{left:751px;top:1054px;font-size:27px;font-weight:500}
  .social-dot{position:absolute;left:748px;top:1101px;width:38px;height:38px;border-radius:50%;background:var(--bronze)}
  .handle{left:800px;top:1107px;font-size:29px;font-weight:700}
</style>
</head>
<body>
<main class="flyer">

  <div class="hero-photo" role="img" aria-label="Smiling construction project manager in a grey suit holding a yellow hard hat and rolled plans"></div>

  <div class="brand">
    <span class="name">VELSTRIDE</span>
    <span class="sub">builders</span>
  </div>

  <div class="abs eyebrow">WE’RE</div>
  <div class="abs headline">Hiring</div>
  <div class="abs role-kicker">CONSTRUCTION</div>
  <div class="abs role-title">Project Manager</div>

  <div class="abs exp-number">5+</div>
  <div class="abs exp-years">YEARS</div>
  <div class="abs exp-label">Experience</div>
  <div class="abs exp-field">in Residential Project<br>Management</div>

  <div class="portfolio-pill">with a strong portfolio of completed homes</div>

  <svg class="requirements-panel" width="740" height="440" viewBox="0 0 740 440" aria-hidden="true">
    <path d="M0 0 H728 L660 414 Q655 436 630 436 H0 Z" fill="var(--panel)"/>
  </svg>

  <ul class="requirements">
    <li class="requirement" style="top:0">
      <svg class="tick" viewBox="0 0 22 22"><circle cx="11" cy="11" r="9.5" fill="none" stroke="#fff" stroke-width="1.6"/><path d="M6.8 11.2l2.8 2.8 5.6-5.6" fill="none" stroke="#fff" stroke-width="1.8"/></svg>
      <span class="title">Excellent leadership skills</span>
      <span class="detail">leads teams with confidence and clarity</span>
      <span class="divider" style="width:570px"></span>
    </li>
    <li class="requirement" style="top:74px">
      <svg class="tick" viewBox="0 0 22 22"><circle cx="11" cy="11" r="9.5" fill="none" stroke="#fff" stroke-width="1.6"/><path d="M6.8 11.2l2.8 2.8 5.6-5.6" fill="none" stroke="#fff" stroke-width="1.8"/></svg>
      <span class="title">Communicates seamlessly</span>
      <span class="detail">with architects, engineers, designers and clients</span>
      <span class="divider" style="width:556px"></span>
    </li>
    <li class="requirement" style="top:148px">
      <svg class="tick" viewBox="0 0 22 22"><circle cx="11" cy="11" r="9.5" fill="none" stroke="#fff" stroke-width="1.6"/><path d="M6.8 11.2l2.8 2.8 5.6-5.6" fill="none" stroke="#fff" stroke-width="1.8"/></svg>
      <span class="title">Knows how to manage</span>
      <span class="detail">budgets and timelines without compromising quality</span>
      <span class="divider" style="width:542px"></span>
    </li>
    <li class="requirement" style="top:222px">
      <svg class="tick" viewBox="0 0 22 22"><circle cx="11" cy="11" r="9.5" fill="none" stroke="#fff" stroke-width="1.6"/><path d="M6.8 11.2l2.8 2.8 5.6-5.6" fill="none" stroke="#fff" stroke-width="1.8"/></svg>
      <span class="title">Solves problems</span>
      <span class="detail">with a positive solution first mindset</span>
      <span class="divider" style="width:520px"></span>
    </li>
    <li class="requirement" style="top:296px">
      <svg class="tick" viewBox="0 0 22 22"><circle cx="11" cy="11" r="9.5" fill="none" stroke="#fff" stroke-width="1.6"/><path d="M6.8 11.2l2.8 2.8 5.6-5.6" fill="none" stroke="#fff" stroke-width="1.8"/></svg>
      <span class="title">Pays attention to every detail</span>
      <span class="detail">because in luxury the small things are the big things</span>
    </li>
  </ul>

  <div class="abs tagline">Build <b>Luxury.</b> Lead <b>Excellence.</b></div>
  <div class="abs website">www.<span>velstridebuilders</span>.com</div>

  <svg class="location-band" width="1200" height="1200" viewBox="0 0 1200 1200" aria-hidden="true">
    <path d="M718 847 H1200 V955 H700 Q686 955 689 942 L706 858 Q709 847 718 847 Z" fill="var(--bronze)"/>
  </svg>
  <div class="abs location-label">LOCATION</div>
  <div class="abs location-name">Bergen County, NJ</div>

  <div class="abs cta">Apply Now</div>
  <div class="abs cta-note">Link in Bio or DM to connect.</div>
  <span class="social-dot" aria-hidden="true"></span>
  <div class="abs handle">velstridebuilders</div>

</main>
</body>
</html>
```